KDWB Business Card

Looking for a business card design to incorporate our branding. We want to only use the colors listing in the Branding Package (attached).
Updates

Target Market(s)

People who need their phone or device fixed.

Industry/Entity Type

Electronics

Contact Information for Business Card

Please use:

Brightwick Gadget Clinic LLC
4810 E Harlow Ridge Rd
Suite 417
San Antonio, TX 78163

Marcus Delgrove, Store Manager

(210) 555-0147

Requirements
Must have
• Must include the colors that are contained within the Branding Package PDF file.

```html
<!DOCTYPE html>
<html lang="en">
<head>
<meta charset="utf-8">
<title>Brightwick Gadget Clinic – Business Card</title>
<link rel="stylesheet" href="https://fonts.googleapis.com/css2?family=Roboto:wght@300;400&display=swap">
<style>
  :root {
    --brand-orange: #f04e23;
    --brand-charcoal: #545456;
    --ink: #2b2b2b;
    --card: #ffffff;
    --backdrop: #e4e4e4;
    --photo-light: #f1f1f5;
    --photo-blue: #e1e3f0;
  }
  * { margin: 0; padding: 0; box-sizing: border-box; }
  html, body { width: 1189px; height: 1200px; overflow: hidden; }
  body {
    background: var(--backdrop);
    font-family: "Roboto", Arial, sans-serif;
    position: relative;
  }
  .card {
    position: absolute;
    left: 263px;
    width: 663px;
    height: 392px;
    background: var(--card);
    overflow: hidden;
  }
  .card--front { top: 188px; }
  .card--back { top: 620px; }

  .card__photo {
    position: absolute;
    inset: 0;
    background:
      radial-gradient(ellipse at 45% 55%, var(--photo-blue) 0%, var(--photo-light) 55%, #fafafa 100%);
  }

  .brand {
    position: absolute;
    display: flex;
    align-items: center;
    gap: 14px;
    transform: translateX(-50%);
    left: 50%;
  }
  .brand__mark {
    width: 56px;
    height: 56px;
    background: var(--brand-orange);
    flex: none;
  }
  .brand__name {
    color: var(--brand-orange);
    font-weight: 400;
    font-size: 30px;
    white-space: nowrap;
  }
  .card--front .brand { top: 165px; }
  .card--back .brand { top: 58px; }

  .side-bar {
    position: absolute;
    left: 0;
    top: 196px;
    width: 29px;
    height: 147px;
    background: var(--brand-charcoal);
  }
  .contact-list {
    position: absolute;
    left: 56px;
    top: 228px;
    list-style: none;
  }
  .contact-list li {
    display: flex;
    align-items: center;
    gap: 10px;
    font-size: 16px;
    color: var(--ink);
    height: 25px;
  }
  .contact-list li + li { margin-top: 2px; }
  .contact-list li:first-child { margin-bottom: 6px; }
  .contact-icon { width: 15px; height: 15px; flex: none; }

  .person {
    position: absolute;
    right: 38px;
    top: 244px;
    text-align: right;
  }
  .person__name {
    font-weight: 300;
    font-size: 25px;
    color: var(--ink);
    letter-spacing: -0.3px;
  }
  .person__title {
    font-size: 15px;
    color: var(--brand-orange);
    margin-top: 1px;
  }
  .accent-bar {
    position: absolute;
    right: 0;
    top: 241px;
    width: 21px;
    height: 57px;
    background: var(--brand-orange);
  }
</style>
</head>
<body>
  <section class="card card--front">
    <div class="card__photo" role="img" aria-label="Faded photo of hands repairing an opened smartphone on a blue mat"></div>
    <div class="brand">
      <span class="brand__mark"></span>
      <span class="brand__name">Brightwick Gadget Clinic</span>
    </div>
  </section>

  <section class="card card--back">
    <div class="brand">
      <span class="brand__mark"></span>
      <span class="brand__name">Brightwick Gadget Clinic</span>
    </div>

    <div class="side-bar"></div>

    <ul class="contact-list">
      <li>
        <svg class="contact-icon" viewBox="0 0 15 15" aria-hidden="true">
          <rect width="15" height="15" fill="var(--brand-orange)"/>
          <path d="M5 3.5 L6.5 5.5 L5.6 6.6 Q6.6 8.6 8.4 9.4 L9.5 8.5 L11.5 10 L10.5 11.5 Q6.5 11.5 3.5 4.5 Z" fill="#fff"/>
        </svg>
        (210) 555-0147
      </li>
      <li>
        <svg class="contact-icon" viewBox="0 0 15 15" aria-hidden="true">
          <rect width="15" height="15" fill="var(--brand-orange)"/>
          <rect x="3" y="4.5" width="9" height="6" fill="none" stroke="#fff" stroke-width="1.2"/>
          <path d="M3 4.5 L7.5 8 L12 4.5" fill="none" stroke="#fff" stroke-width="1.2"/>
        </svg>
        marcus@BrightwickGadget.com
      </li>
      <li>
        <svg class="contact-icon" viewBox="0 0 15 15" aria-hidden="true">
          <rect width="15" height="15" fill="var(--brand-orange)"/>
          <circle cx="7.5" cy="7.5" r="4" fill="none" stroke="#fff" stroke-width="1.2"/>
          <path d="M3.5 7.5 H11.5 M7.5 3.5 Q5 7.5 7.5 11.5 Q10 7.5 7.5 3.5" fill="none" stroke="#fff" stroke-width="1"/>
        </svg>
        www.BrightwickGadget.com
      </li>
    </ul>

    <div class="person">
      <p class="person__name">Marcus Delgrove</p>
      <p class="person__title">Store Manager</p>
    </div>
    <div class="accent-bar"></div>
  </section>
</body>
</html>
```